Need Business Card for our Real Estate Business with Sales Executive's Picture

PANTONE 484 C ( RED)

PANTONE 2766 C ( BLUE

Industry/Entity Type

Real Estate

Contact Information for Business Card

Name, Mobile, email, & picture of Person
Agency Phone, address, Web address

Requirements
Must have
• Our Logo Colours, Agent Picture,

```html
<!DOCTYPE html>
<html lang="en">
<head>
<meta charset="utf-8">
<title>Voranel Real Estate – Business Card</title>
<link rel="stylesheet" href="https://fonts.googleapis.com/css2?family=Open+Sans:wght@400;600&display=swap">
<style>
  :root {
    --bg: #c9cbce;
    --paper: #ffffff;
    --navy: #0b1638;
    --fold: #7d8291;
    --ink: #4a4a4a;
    --icon: #555555;
    --accent-red: #8e1c1c;
    --photo-top: #2b3f73;
    --photo-bottom: #17244b;
  }
  * { margin: 0; padding: 0; box-sizing: border-box; }
  html, body { width: 1200px; height: 1000px; overflow: hidden; }
  body {
    background: var(--bg);
    font-family: "Open Sans", sans-serif;
    position: relative;
  }
  .card { position: absolute; overflow: hidden; }

  /* Front */
  .card-front {
    left: 262px; top: 85px; width: 682px; height: 389px;
    background: var(--paper);
  }
  .agent-photo {
    position: absolute; left: 36px; top: 40px; width: 124px; height: 160px;
    background: linear-gradient(180deg, var(--photo-top), var(--photo-bottom));
  }
  .brand-small {
    position: absolute; left: 196px; top: 82px; width: 300px;
    display: flex; align-items: center; justify-content: center; gap: 8px;
    color: var(--navy); font-weight: 600; font-size: 22px; letter-spacing: 1px;
    white-space: nowrap; line-height: 1;
  }
  .brand-small .mark { width: 9px; height: 9px; background: var(--accent-red); }
  .agent-name {
    position: absolute; left: 191px; top: 143px;
    font-size: 23px; color: var(--ink); white-space: nowrap;
  }
  .front-rule { position: absolute; left: 0; top: 0; }
  .agent-title {
    position: absolute; left: 175px; top: 185px; width: 343px;
    text-align: center; color: #fff; font-size: 19px; white-space: nowrap;
  }
  .office-address {
    position: absolute; left: 0; top: 224px; width: 682px; padding-left: 10px;
    text-align: center; font-size: 19px; color: var(--ink); white-space: nowrap;
  }
  .contact-list { position: absolute; left: 215px; top: 272px; list-style: none; }
  .contact-list li {
    display: flex; align-items: center; gap: 22px;
    height: 31px; font-size: 19.5px; color: var(--ink); white-space: nowrap;
  }
  .contact-list svg { width: 19px; height: 19px; flex: none; }

  /* Back */
  .card-back {
    left: 262px; top: 525px; width: 680px; height: 388px;
    background: var(--navy);
  }
  .back-tabs { position: absolute; left: 0; top: 0; }
  .brand-large {
    position: absolute; left: 0; top: 214px; width: 680px;
    display: flex; align-items: center; justify-content: center; gap: 14px;
    color: #fff; font-weight: 600; font-size: 42px; letter-spacing: 4px;
    white-space: nowrap; line-height: 1;
  }
  .brand-large .mark { width: 13px; height: 13px; background: var(--accent-red); }
</style>
</head>
<body>

<section class="card card-front">
  <div class="agent-photo" role="img" aria-label="Portrait photo of the sales executive"></div>

  <div class="brand-small"><span class="mark"></span><span>VORANEL</span></div>

  <p class="agent-name">Name of Sales Executive's</p>

  <svg class="front-rule" width="682" height="389" viewBox="0 0 682 389" aria-hidden="true">
    <rect x="0" y="205" width="682" height="3" fill="var(--navy)"/>
    <polygon points="166,206 175,180 185,206" fill="var(--fold)"/>
    <polygon points="508,180 518,206 528,206" fill="var(--fold)"/>
    <path d="M175,180 L518,180 L508,212 Q506,218 498,218 L195,218 Q187,218 185,212 Z" fill="var(--navy)"/>
  </svg>
  <p class="agent-title">Sales Executive</p>

  <p class="office-address">address of Voranel Real Estate</p>

  <ul class="contact-list">
    <li>
      <svg viewBox="0 0 18 18" aria-hidden="true"><circle cx="9" cy="9" r="7.5" fill="none" stroke="var(--icon)" stroke-width="1.6"/><path d="M6.3,5 L7.6,5 L8.2,7 L7.3,7.8 Q8,9.7 10.2,10.7 L11,9.8 L13,10.4 L13,11.7 Q12.6,12.8 11,12.6 Q6.4,11.6 5.4,6.9 Q5.3,5.4 6.3,5 Z" fill="var(--icon)"/></svg>
      <span>mobile / agency phone</span>
    </li>
    <li>
      <svg viewBox="0 0 18 18" aria-hidden="true"><rect x="1" y="4" width="16" height="11" fill="var(--icon)"/><path d="M1,4 L9,10.5 L17,4" fill="none" stroke="#fff" stroke-width="1.2"/></svg>
      <span>voranel@email.com</span>
    </li>
    <li>
      <svg viewBox="0 0 18 18" aria-hidden="true"><circle cx="9" cy="9" r="7.5" fill="var(--icon)"/><g fill="none" stroke="#fff" stroke-width="1"><ellipse cx="9" cy="9" rx="3.3" ry="7.5"/><line x1="1.5" y1="9" x2="16.5" y2="9"/><line x1="9" y1="1.5" x2="9" y2="16.5"/><path d="M2.8,5 H15.2 M2.8,13 H15.2"/></g></svg>
      <span>www.web address.com</span>
    </li>
  </ul>
</section>

<section class="card card-back">
  <svg class="back-tabs" width="680" height="388" viewBox="0 0 680 388" aria-hidden="true">
    <path d="M60,0 L616,0 L582,50 Q573,63 558,63 L122,63 Q107,63 98,50 Z" fill="var(--paper)"/>
    <path d="M122,326 L558,326 Q573,326 582,339 L616,388 L60,388 L98,339 Q107,326 122,326 Z" fill="var(--paper)"/>
  </svg>
  <div class="brand-large"><span class="mark"></span><span>VORANEL</span></div>
</section>

</body>
</html>
```